B2B Case Study Template Design (InDesign or Affinity Designer)

Hello,We are a company specializing in custom sanitary space fit-outs and Solid Surface manufacturing. We are looking for a talented layout designer to create a professional and modern "Case Study" template to showcase our projects.This template must strictly be designed using Adobe InDesign or Affinity Designer. We do not want Canva, Word, or PowerPoint files.Attached, there is a file you can reference named "Brelo - Case Study.pdf". This is our previous layout.

Your mission is to recreate this case study using our new brand guidelines (which I will also provide) while using the exact same texts, photos, and sections (Key Data / "Données clés", Valkor's Role / "Le rôle d'Valkor", Valkor Products / "Produits Valkor").

Note: This project is the first of a series. We want to keep everything in the same project scope moving forward. If the work is satisfactory, we will hire you directly for upcoming print materials (flyer templates, catalogs, etc.).

---
2 Exemples of existing Case Studies : BRELO and TOLVEN
1 Full INDISIGN assembled file for MURESK project (you can work from there)
The logo (multi format)
And a zip file with the PATTERN, FONT and LOGO ALTERNATIVES (for graphic use only - on a photo, or else)

Target Market(s)

Building professionals, architects, specifiers, B2B companies, and contractors.

Industry/Entity Type

Architecture / Construction / B2B

Font styles to use
Sans Serif

Requirements
Must have
• The final source file must be delivered in Adobe InDesign (.indd/.idml) or Affinity Designer format. The design must be clean, structured, and highlight the architectural photography. Paragraph and character styles must be properly set up in the software so we can easily edit the text ourselves in the future. Strict integration of our new brand guidelines (colors, typography).
Nice to have
• A modular design: a layout that works perfectly for a 2-page (front/back) document, but can be easily expanded to 3 or 4 pages if a specific case study requires more content. Layout suggestions for recurring graphic elements (e.g., custom icons for key data, elegant frames for pull quotes).
Should not have
• Do NOT use Canva, Microsoft Word, or Photoshop for the layout. Avoid cluttered, overly colorful, or whimsical designs. We are looking for a premium, high-end, and serious aesthetic suited for the architectural field.

```html
<!DOCTYPE html>
<html lang="fr">
<head>
<meta charset="utf-8">
<title>Nordal – Projet Muresk – Étude de cas</title>
<link rel="stylesheet" href="https://fonts.googleapis.com/css2?family=Poppins:wght@300;400;500;600;700;800&display=swap">
<style>
:root{
  --stage:#dcdcdc;
  --sand:#ece3d3;
  --clay:#9b7262;
  --ink:#2a2a2a;
  --soft-ink:#4a4a4a;
  --paper:#ffffff;
}
*{margin:0;padding:0;box-sizing:border-box}
html,body{width:1200px;height:3610px;overflow:hidden;background:var(--stage)}
body{font-family:"Poppins",sans-serif;color:var(--ink);position:relative}
.spread{position:absolute;left:98px;width:1005px;height:711px;background:var(--paper);overflow:hidden;box-shadow:0 2px 6px rgba(0,0,0,.18)}
.spread-cover{top:156px;background:var(--sand)}
.spread-challenge{top:928px;background:var(--sand)}
.spread-gallery{top:1700px}
.spread-method{top:2474px}
.block{position:absolute}
.photo-washroom{background:linear-gradient(180deg,#5f6a4f 0%,#6f7a5d 30%,#d8d6cf 45%,#f2f0eb 52%,#8a6547 60%,#7a5a3f 82%,#cfc9bf 100%)}
.photo-tall{background:linear-gradient(180deg,#d9dad6 0%,#5f6a4f 14%,#6c7658 38%,#dcd9d2 46%,#f3f1ec 52%,#8a6547 60%,#71533a 80%,#c9c3b9 100%)}
.drawing-panel{background:linear-gradient(180deg,#a9a9a9,#9c9c9c)}
.brand{font-weight:500;letter-spacing:.28em;color:var(--ink)}
.contact-card{background:var(--paper);padding:52px 0 0 51px}
.contact-card .rule{width:24px;height:1px;background:var(--ink);margin-bottom:14px}
.contact-card h3{font-size:12.5px;font-weight:700;margin-bottom:12px}
.contact-card p{font-size:8.5px;line-height:1.45;margin-bottom:12px}
.cover-title{color:var(--paper);font-weight:800;text-shadow:0 2px 6px rgba(0,0,0,.45)}
.cover-title h1{font-size:35px;line-height:1;margin-bottom:32px;letter-spacing:.01em}
.cover-title h2{font-size:25px;line-height:1.35;font-weight:800}
.heading-light{font-weight:300;font-size:24px;line-height:1.3;text-transform:uppercase;letter-spacing:.01em}
.lede{font-size:10px;line-height:1.35}
.body{font-size:8.8px;line-height:1.45;color:var(--soft-ink)}
.overlay-caption{background:rgba(236,227,211,.92);padding:10px 16px;font-size:20px;font-weight:300;line-height:1.2}
.label{font-size:12px;font-weight:700;text-transform:uppercase}
.bullets{list-style:disc;padding-left:16px;font-size:8.4px;line-height:1.4}
.product{position:absolute;text-align:center;width:110px}
.product .disc{width:82px;height:82px;border-radius:50%;border:2px solid var(--ink);margin:0 auto 8px;background:linear-gradient(180deg,#eeeeec,#b9b7b2)}
.product span{font-size:7.5px;font-weight:500;text-transform:uppercase;line-height:1.25;display:block}
.step-title{font-size:14px;font-weight:400;margin-bottom:16px}
.step-text{font-size:8.2px;line-height:1.5;font-weight:500;margin-bottom:12px}
.band{position:absolute;top:0;height:140px;width:503px}
.band-sand{left:0;background:var(--sand)}
.band-clay{left:502px;background:var(--clay);color:var(--paper)}
.band h2{position:absolute;left:50px;top:35px;font-weight:300;font-size:24px;line-height:1.3;text-transform:uppercase}
.band-clay h2{left:57px}
.band p{position:absolute;left:57px;top:110px;font-size:10px}
.intro-bold{font-size:11.5px;font-weight:700;line-height:1.22}
.accent{color:var(--clay);font-weight:600}
.method-list{font-size:8.6px;line-height:1.45;color:var(--soft-ink)}
.method-list .item{margin-bottom:14px}
.method-list .item>.accent{display:block}
.gutter{position:absolute;left:502px;top:0;width:1px;height:100%;background:rgba(0,0,0,.08)}
</style>
</head>
<body>

<section class="spread spread-cover">
  <div class="block photo-washroom" style="left:251px;top:0;width:754px;height:711px" role="img" aria-label="Photo d'un sanitaire rénové : double vasque blanche sur meuble en bois, miroir et murs vert olive"></div>
  <div class="block brand" style="left:46px;top:208px;font-size:30px">NORDAL</div>
  <div class="block brand" style="left:533px;top:25px;font-size:44px">NORDAL</div>
  <div class="block contact-card" style="left:158px;top:255px;width:244px;height:342px">
    <div class="rule"></div>
    <h3>Prendre contact.</h3>
    <p>Adresse</p>
    <p>12 Rue des Tilleuls,<br>43200 Varenne<br>France.</p>
    <p>Site Web</p>
    <p>www.valkor.fr<br>info@valkor.fr</p>
    <p>Téléphone</p>
    <p>+33 4 00 12 34 56</p>
  </div>
  <div class="block cover-title" style="left:533px;top:503px">
    <h1>PROJET MURESK</h1>
    <h2>L'ART DE L'AGILITÉ :<br>RÉNOVATION SANITAIRE<br>EN SITE OCCUPÉ</h2>
  </div>
</section>

<section class="spread spread-challenge">
  <div class="block photo-washroom" style="left:0;top:0;width:502px;height:331px" role="img" aria-label="Photo d'un bloc sanitaire avec double vasque, miroir et sèche-mains"></div>
  <div class="block overlay-caption" style="left:31px;top:243px;width:352px;height:88px">Projet Muresk : quand la performance s'adapte à la continuité de service</div>

  <div class="block" style="left:561px;top:36px;width:420px">
    <h2 class="heading-light">Une prouesse d'agilité :<br>le défi du site occupé</h2>
    <p class="lede" style="margin-top:20px">Maintenir le confort des usagers<br>pendant la mutation des espaces.</p>
    <p class="body" style="margin-top:24px">L'enjeu majeur du chantier Muresk résidait dans l'environnement immédiat :<br>des open spaces occupés par des collaborateurs en plein travail.<br>Ce projet « Muresk » exigeait donc une discrétion absolue<br>et une rapidité d'exécution chirurgicale.</p>
  </div>

  <div class="block" style="left:0;top:331px;width:383px;height:380px;background:var(--paper)">
    <p class="body" style="position:absolute;left:45px;top:12px;width:325px">L'enjeu majeur du chantier Muresk résidait dans l'environnement immédiat : des open spaces occupés par des collaborateurs en plein travail.<br>Ce projet exigeait donc une discrétion absolue et une rapidité d'exécution chirurgicale, dans le but de maintenir le confort des usagers pendant la transformation des espaces sanitaires.</p>
    <div style="position:absolute;left:31px;top:109px;width:170px">
      <div class="label">Données clé</div>
      <ul class="bullets" style="margin-top:10px">
        <li>Lieu : 12 Avenue de Muresk, Paris 17e (Immeuble bureaux Premium)</li>
        <li>Maître d'ouvrage : Ardent Banque</li>
        <li>Maître d'œuvre : Kestra</li>
        <li>Livraison : 2026</li>
      </ul>
    </div>
    <div style="position:absolute;left:207px;top:109px;width:165px">
      <div class="label">Le rôle d'Valkor</div>
      <ul class="bullets" style="margin-top:10px">
        <li>Conception de mobilier VELTIS sur-mesure à profondeur variable</li>
        <li>Planification de pose par tranches</li>
        <li>Logistique de propreté «Zéro Poussière»</li>
        <li>Installation en mode «Discret»</li>
      </ul>
    </div>
    <div class="label" style="position:absolute;left:31px;top:228px">Produits Valkor</div>
    <div class="product" style="left:17px;top:245px"><div class="disc" role="img" aria-label="Vignette de la vasque"></div><span>Vasque Orna VO-18</span></div>
    <div class="product" style="left:128px;top:245px"><div class="disc" role="img" aria-label="Vignette du support de mobilier"></div><span>Support Veltisol<br>sur-mesure</span></div>
    <div class="product" style="left:233px;top:245px"><div class="disc" role="img" aria-label="Vignette du miroir"></div><span>Miroir<br>sur mesure</span></div>
  </div>

  <div class="block photo-tall" style="left:503px;top:331px;width:219px;height:380px" role="img" aria-label="Photo d'une vasque individuelle sur meuble bois dans un sanitaire vert olive"></div>

  <div class="block" style="left:747px;top:336px;width:235px">
    <h3 class="step-title">1. Mode «Discret» &amp; propreté :</h3>
    <p class="step-text">Travailler dans le silence et sans dégagement de poussière était une condition non négociable.</p>
    <p class="step-text">Valkor a mis en place un protocole spécifique pour garantir une propreté absolue des parties communes et des sanitaires, permettant aux occupants de continuer leurs activités sans nuisance.</p>
    <h3 class="step-title" style="margin-top:24px">2. Flux de travail «Chrono» :</h3>
    <p class="step-text">Pour éviter la fermeture simultanée de tous les sanitaires de l'immeuble, Valkor a orchestré une pose par tranches successives.</p>
    <p class="step-text">Ce phasage dynamique a permis de maintenir la continuité de service pour le client tout en assurant un temps de travaux record par étage.</p>
  </div>
</section>

<section class="spread spread-gallery">
  <div class="block photo-tall" style="left:0;top:0;width:502px;height:711px" role="img" aria-label="Photo d'un sanitaire avec double vasque blanche sur meuble bois, murs vert olive et carrelage clair"></div>
  <div class="block photo-tall" style="left:503px;top:0;width:502px;height:711px" role="img" aria-label="Photo d'une vasque individuelle sur meuble bois avec sèche-mains mural"></div>
</section>

<section class="spread spread-method">
  <div class="band band-sand">
    <h2>Mobilier Veltis :<br>l'intelligence du sur-mesure</h2>
    <p>S'adapter à l'existant sans compromis sur le design.</p>
  </div>
  <div class="band band-clay">
    <h2>De la conception à la pose :<br>la maîtrise de A à Z</h2>
    <p>Une responsabilité totale pour un résultat garanti.</p>
  </div>
  <div class="gutter"></div>

  <p class="block intro-bold" style="left:29px;top:175px;width:215px">Le projet Muresk a nécessité une adaptation rare de notre gamme de supports de fixation.</p>
  <div class="block photo-tall" style="left:266px;top:147px;width:146px;height:266px" role="img" aria-label="Photo d'une vasque sur meuble bois installée"></div>
  <div class="block drawing-panel" style="left:184px;top:383px;width:307px;height:311px" role="img" aria-label="Plans techniques du meuble sur-mesure : élévation cotée et vue en perspective"></div>
  <div class="block method-list" style="left:29px;top:372px;width:148px">
    <span class="accent">Profondeurs atypiques :</span>
    <ul class="bullets" style="margin-top:14px">
      <li>Le bureau d'études Valkor a redessiné le mobilier VELTISOL pour répondre à des profondeurs de niches sortant des standards habituels, optimisant ainsi chaque centimètre carré d'espace.</li>
      <li>De plus, la redéfinition du support a permis l'ajout de rangements sous-jacents, permettant le stockage de matériel d'entretien, etc.</li>
    </ul>
  </div>

  <p class="block intro-bold" style="left:571px;top:161px;width:380px">Au-delà de la technique, ce projet représente également comment la société Valkor prend la responsabilité du résultat final en assurant elle-même la pose de ses produits.</p>
  <div class="block method-list" style="left:571px;top:237px;width:380px">
    <div class="item"><span class="accent">• Manutention maîtrisée : Une logistique invisible en milieu occupé</span>Livraison et acheminement en milieu occupé sans perturber les flux de l'immeuble, en dehors des pics d'affluence.</div>
    <div class="item"><span class="accent">• Précision de pose : L'ingénierie face aux contraintes de la rénovation</span>Ajustement des structures sur-mesure sur des supports existants parfois irréguliers &amp; redimensionnement du mobilier Veltis pour s'adapter aux contraintes présentes et modification de sa profondeur.</div>
  </div>
  <div class="block photo-washroom" style="left:571px;top:343px;width:376px;height:179px" role="img" aria-label="Photo de chantier annotée de cotes de pose pour le meuble vasque"></div>
  <div class="block method-list" style="left:571px;top:544px;width:380px">
    <div class="item"><span class="accent">• Engagement rapidité : un phasage précis pour la continuité de service</span>L'installation a été orchestrée par tranches successives pour éviter la fermeture simultanée de tous les points d'eau et maintenir le confort des collaborateurs.</div>
    <div class="item" style="padding-left:8px">Grâce à un pré-montage maximal dans notre atelier du Val d'Arlen, le temps d'intervention physique sur le site de Muresk a été réduit au strict minimum.</div>
    <div class="item" style="padding-left:8px">Chaque journée s'est conclue par un nettoyage rigoureux «fin de poste», permettant une restitution immédiate des locaux, sans poussière ni nuisances.</div>
  </div>
</section>

</body>
</html>
```